Personal training and nutrition business needs business card design

We need a business card that outlays our services and invites potential customers to join our team and take the first step to a healthier and more enjoyable life. We cater for any level of fitness and specialize in weight loss and conditioning, strength training, muscle gain and strength endurance. Whether you are just starting off or need some help getting to the next level of your journey we are here to get the job done.
We specialize in one on one or one on two personal training sessions and each program will be custom made to suit individual fitness goals of our clients

```html
<!DOCTYPE html>
<html lang="en">
<head>
<meta charset="utf-8">
<title>Stride &amp; Tempo – Business Card</title>
<link rel="stylesheet" href="https://fonts.googleapis.com/css2?family=Lato:wght@400;700&family=Oswald:wght@400;500&display=swap">
<style>
  :root {
    --page-bg: #2b2b2e;
    --card-bg: #171717;
    --purple: #a45ec8;
    --purple-deep: #7c4cc0;
    --text-light: #f2f2f2;
    --divider: #8a8a8a;
  }
  * { box-sizing: border-box; margin: 0; padding: 0; }
  html, body {
    width: 1200px; height: 900px; overflow: hidden;
    background: var(--page-bg);
    font-family: "Lato", sans-serif;
    color: var(--text-light);
  }
  .canvas {
    width: 1200px; height: 900px;
    display: flex; flex-direction: column;
    align-items: center; justify-content: center;
    gap: 44px;
  }
  .card {
    position: relative;
    width: 600px; height: 343px;
    background: var(--card-bg);
    box-shadow: 0 14px 30px rgba(0,0,0,.45);
    overflow: hidden;
  }
  .card__band {
    position: absolute; left: 0; right: 0; bottom: 0;
    height: 13px;
    background: linear-gradient(90deg, var(--purple-deep), var(--purple));
  }

  /* Front */
  .card--front {
    display: flex; align-items: center; justify-content: center;
  }
  .brand { display: flex; flex-direction: column; align-items: flex-start; margin-bottom: 10px; }
  .brand__row { display: flex; align-items: center; gap: 18px; }
  .brand__mark {
    width: 58px; height: 58px;
    background: var(--purple);
    border-radius: 8px;
  }
  .brand__name {
    font-family: "Lato", sans-serif;
    font-weight: 700;
    font-size: 44px;
    letter-spacing: 2px;
    text-transform: uppercase;
    color: var(--text-light);
    line-height: 1;
  }
  .brand__tagline {
    margin-top: 12px;
    margin-left: 76px;
    font-family: "Oswald", sans-serif;
    font-weight: 400;
    font-size: 14px;
    letter-spacing: 2.4px;
    text-transform: uppercase;
    color: var(--purple);
  }

  /* Back */
  .card--back { padding: 92px 0 0 0; }
  .back__top { display: flex; align-items: center; padding-left: 70px; }
  .person { text-align: right; width: 200px; }
  .person__name {
    font-family: "Oswald", sans-serif;
    font-weight: 500;
    font-size: 30px;
    letter-spacing: .5px;
    text-transform: uppercase;
    color: var(--purple);
    line-height: 1.1;
  }
  .person__role { font-size: 17px; color: var(--text-light); margin-top: 2px; }
  .back__divider {
    width: 1px; height: 92px;
    background: var(--divider);
    margin: 0 26px;
  }
  .contacts { list-style: none; display: flex; flex-direction: column; gap: 6px; }
  .contacts__item { display: flex; align-items: center; gap: 10px; font-size: 18px; }
  .contacts__icon { width: 17px; height: 17px; flex: none; }
  .address {
    margin-top: 48px;
    padding-left: 70px;
    font-size: 18px;
    letter-spacing: .3px;
  }
</style>
</head>
<body>
<main class="canvas">
  <section class="card card--front" aria-label="Card front">
    <div class="brand">
      <div class="brand__row">
        <span class="brand__mark" aria-hidden="true"></span>
        <span class="brand__name">Stride &amp; Tempo</span>
      </div>
      <p class="brand__tagline">Personal Training. Nutrition. Motivation</p>
    </div>
    <div class="card__band"></div>
  </section>

  <section class="card card--back" aria-label="Card back">
    <div class="back__top">
      <div class="person">
        <p class="person__name">Jonathan Smith</p>
        <p class="person__role">Managing Director</p>
      </div>
      <div class="back__divider"></div>
      <ul class="contacts">
        <li class="contacts__item">
          <svg class="contacts__icon" viewBox="0 0 24 24" fill="none" stroke="#a45ec8" stroke-width="2.2" stroke-linecap="round" stroke-linejoin="round"><path d="M22 16.9v3a2 2 0 0 1-2.2 2 19.8 19.8 0 0 1-8.6-3.1 19.5 19.5 0 0 1-6-6A19.8 19.8 0 0 1 2.1 4.2 2 2 0 0 1 4.1 2h3a2 2 0 0 1 2 1.7c.1 1 .4 1.9.7 2.8a2 2 0 0 1-.5 2.1L8 9.9a16 16 0 0 0 6 6l1.3-1.3a2 2 0 0 1 2.1-.4c.9.3 1.8.6 2.8.7a2 2 0 0 1 1.7 2z"/></svg>
          <span>044-123 456 789</span>
        </li>
        <li class="contacts__item">
          <svg class="contacts__icon" viewBox="0 0 24 24" fill="#a45ec8"><path d="M2 5h20v14H2z"/><path d="M2 5l10 8 10-8" fill="none" stroke="#171717" stroke-width="1.8"/></svg>
          <span>info@webname.com</span>
        </li>
        <li class="contacts__item">
          <svg class="contacts__icon" viewBox="0 0 24 24" fill="none" stroke="#a45ec8" stroke-width="2"><circle cx="12" cy="12" r="10"/><path d="M2 12h20M12 2c3 3 3 17 0 20M12 2c-3 3-3 17 0 20"/></svg>
          <span>www.websitename.com</span>
        </li>
      </ul>
    </div>
    <p class="address">421, Address line here, Country Name, 45452</p>
    <div class="card__band"></div>
  </section>
</main>
</body>
</html>
```